Financial Services Consultant needs a business card

We need a business card for a new consulting company based in Melbourne called
"Quelbrook Insights". Tagline is Measure, Monitor, Save
We would like to see business card designs that are in line with the minimal style of the website www.quelbrook-insights.example
The font I have used on the website is Proxima Nova and would like the same or similar font used on the business card with a minimal design in line with the website Two sided with "QUELBROOK INSIGHTS" MEASURE, MONITOR, SAVE on one side and name, title and contact details on the otther
Updates

Hi All, thanks for your submissions, much appreciated.

I have recently added some colour to my webiste, it is hex #3a7b74 for those that wish to use it
Thanks

Hi all

thanks very much for your design submissions I am very impressed and they are much appreciated.

Interms of general feedback please find below;

Colour: I am trying to stick to a minimal design and colour scheme for my website which is still under construction, up to 3 colours( www.quelbrook-insights.example) it is currently black and white with a small amount of blue/green but I am open to suggestion/interpretations for a consulting company.

Card: I dont mind if it has rounded edges or straight, I was thinking about using a letterpress card if possible

Detail: the detail on the card will include; Name, Title, Mobile, Personal Email, Business Email,Web,Business Address

Once again thanks for submissions

Industry/Entity Type

Business

```html
<!DOCTYPE html>
<html lang="en">
<head>
<meta charset="utf-8">
<title>Quelbrook Insights — Business Card</title>
<link rel="stylesheet" href="https://fonts.googleapis.com/css2?family=Montserrat:wght@400;500;600;700&display=swap">
<style>
  :root {
    --page-bg: #f4f4f4;
    --card-bg: #ffffff;
    --ink: #000000;
    --teal: #3a7b74;
    --rule: #e2e2e2;
    --card-edge: #c9c9c9;
    --card-border-dark: #222222;
  }

  * { box-sizing: border-box; margin: 0; padding: 0; }

  html, body {
    width: 1200px;
    height: 391px;
    overflow: hidden;
    background: var(--page-bg);
    font-family: "Montserrat", Arial, sans-serif;
    color: var(--ink);
  }

  .sheet {
    position: relative;
    width: 1200px;
    height: 391px;
  }

  .card {
    position: absolute;
    background: var(--card-bg);
    overflow: hidden;
  }

  /* Front side */
  .card--front {
    left: 16px;
    top: 17px;
    width: 564px;
    height: 356px;
    border: 1px solid var(--card-edge);
    box-shadow: 1px 2px 3px rgba(0, 0, 0, 0.18);
  }

  .front__name {
    position: absolute;
    left: 0;
    right: 0;
    top: 150px;
    text-align: center;
    font-weight: 500;
    font-size: 38px;
    letter-spacing: 1px;
    line-height: 1;
  }

  .front__tagline {
    position: absolute;
    left: 0;
    right: 0;
    top: 212px;
    text-align: center;
    font-weight: 700;
    font-size: 11px;
    letter-spacing: 0.6px;
    color: var(--teal);
  }

  /* Back side */
  .card--back {
    left: 623px;
    top: 16px;
    width: 562px;
    height: 358px;
    border: 1px solid var(--card-border-dark);
  }

  .back__brand {
    position: absolute;
    left: 0;
    right: 0;
    top: 0;
    height: 199px;
    border-bottom: 2px solid var(--rule);
    display: flex;
    align-items: center;
    justify-content: flex-end;
    padding-right: 25px;
    gap: 14px;
  }

  .brand__square {
    width: 18px;
    height: 18px;
    background: var(--teal);
    flex: none;
  }

  .brand__name {
    font-weight: 400;
    font-size: 36px;
    line-height: 1;
    color: var(--ink);
  }

  .back__details {
    position: absolute;
    left: 315px;
    top: 225px;
    line-height: 1.25;
  }

  .details__name {
    font-weight: 500;
    font-size: 16.5px;
    letter-spacing: 0.2px;
  }

  .details__line {
    font-weight: 500;
    font-size: 12.5px;
  }

  .back__footer {
    position: absolute;
    left: 0;
    right: 0;
    bottom: 0;
    height: 30px;
    background: var(--teal);
    color: #ffffff;
    font-weight: 500;
    font-size: 13px;
    display: flex;
    align-items: center;
    justify-content: center;
  }
</style>
</head>
<body>
  <main class="sheet">
    <section class="card card--front" aria-label="Card front">
      <h1 class="front__name">QUELBROOK INSIGHTS</h1>
      <p class="front__tagline">MEASURE , MONITOR , SAVE</p>
    </section>

    <section class="card card--back" aria-label="Card back">
      <div class="back__brand">
        <span class="brand__square" aria-hidden="true"></span>
        <span class="brand__name">Quelbrook Insights</span>
      </div>

      <div class="back__details">
        <p class="details__name">FIRST NAME LAST NAME</p>
        <p class="details__line">TITLE</p>
        <p class="details__line">Address goes here</p>
        <p class="details__line">+91-5550123456</p>
      </div>

      <footer class="back__footer">www.quelbrook-insights.example</footer>
    </section>
  </main>
</body>
</html>
```